Luxury Business Card Design for High-End Window Treatments

Gilded Slatworks
Custom Plantation Shutters & Architectural Shading Systems

⸻

BACK

Daniel Trevick
Owner

Custom Interior & Exterior Window Treatments

919-555-0148
gildedslatworks.com

I have included a picture that I’m hoping we can use on the back, but I’m also wondering if you can get rid of the ladder? Should we get rid of shutters , shades and blinds underneath Gilded Slatworks?

Target Market(s)

High-end residential homeowners, custom home builders, architects, interior designers, and luxury renovation clients seeking premium plantation shutters and motorized architectural shading systems.

Industry/Entity Type

Custom Window treatments

Contact Information for Business Card

Front Gilded Slatworks Custom Plantation Shutters Motorized Architectural Shading Systems BACK Daniel Trevick Owner 919-555-0148 GildedSlatworks.com Custom Interior & Exterior Window Treatments By Appointment

Requirements
Nice to have
• Not 100% sure on nice to halves or the color but you can definitely check out my website to get a better understanding of what I’m trying to do

```html
<!DOCTYPE html>
<html lang="en">
<head>
<meta charset="utf-8">
<title>Gilded Slatworks — Business Card</title>
<link rel="stylesheet" href="https://fonts.googleapis.com/css2?family=Lora:wght@400;600;700&family=Kurale&family=Mulish:wght@400;500&display=swap">
<style>
  :root {
    --backdrop: #1e1c1d;
    --card-black: #0b0b0b;
    --card-black-soft: #151515;
    --gold: #f1c94a;
    --gold-edge: #e0b334;
    --silver: #d9d9d9;
    --ivory: #f3efe6;
    --photo-light: #7d9fc9;
    --photo-dark: #3a3d41;
  }
  * { box-sizing: border-box; margin: 0; padding: 0; }
  html, body {
    width: 1200px; height: 939px; overflow: hidden;
    background: var(--backdrop);
  }
  .canvas {
    width: 1200px; height: 939px;
    display: flex; flex-direction: column; align-items: center; justify-content: center;
    gap: 48px;
  }
  .card {
    position: relative;
    width: 600px; height: 343px;
    border-radius: 18px;
    background: linear-gradient(160deg, var(--card-black-soft), var(--card-black));
    box-shadow: 0 4px 0 var(--gold-edge), 0 18px 40px rgba(0,0,0,.55);
    overflow: hidden;
    color: var(--ivory);
  }

  /* Front */
  .front .brand {
    position: absolute; left: 0; right: 0; top: 92px;
    text-align: center;
  }
  .brand-name {
    font-family: "Lora", serif; font-weight: 400;
    color: var(--silver);
    font-size: 46px; line-height: 1.05; letter-spacing: .5px;
  }
  .product-line {
    margin-top: 14px;
    font-family: "Kurale", serif;
    color: var(--gold);
    font-size: 24px; word-spacing: 14px;
  }
  .front .tagline {
    position: absolute; left: 0; right: 0; bottom: 34px;
    text-align: center;
    font-family: "Lora", serif; font-size: 15px; letter-spacing: .6px;
    color: var(--ivory);
  }

  /* Back */
  .back .photo {
    position: absolute; top: 0; right: 0; bottom: 0; width: 66%;
    background: linear-gradient(180deg, var(--photo-light) 0%, var(--photo-dark) 100%);
  }
  .back .photo-fade {
    position: absolute; inset: 0;
    background: linear-gradient(90deg, var(--card-black) 34%, rgba(11,11,11,.85) 44%, rgba(11,11,11,0) 66%);
  }
  .back .info {
    position: absolute; left: 40px; top: 32px; width: 300px;
  }
  .back .brand-name { font-size: 32px; text-align: left; }
  .back .product-line { font-size: 15px; margin-top: 6px; word-spacing: 8px; }
  .person-name {
    margin-top: 18px;
    font-family: "Lora", serif; font-weight: 700; font-size: 24px;
  }
  .person-role {
    font-family: "Mulish", sans-serif; font-size: 15px; margin-top: 2px; padding-left: 6px;
  }
  .contact { list-style: none; margin-top: 12px; }
  .contact li {
    display: flex; align-items: center; gap: 9px;
    font-family: "Mulish", sans-serif; font-size: 16px; margin-bottom: 4px; padding-left: 8px;
  }
  .contact svg { width: 13px; height: 13px; flex: none; }
  .services {
    margin-top: 16px; padding-left: 8px;
    font-family: "Lora", serif; font-weight: 600; font-size: 16px;
    line-height: 1.2; text-transform: uppercase; letter-spacing: .5px;
  }
</style>
</head>
<body>
<main class="canvas">

  <section class="card front" aria-label="Card front">
    <div class="brand">
      <div class="brand-name">Gilded Slatworks</div>
      <div class="product-line">Shutters Shades Blinds</div>
    </div>
    <p class="tagline">Custom Plantation Shutters &amp; Architectural Shading Systems</p>
  </section>

  <section class="card back" aria-label="Card back">
    <div class="photo" role="img" aria-label="Photo of a large home with a screened porch and exterior shades under a blue sky"></div>
    <div class="photo-fade"></div>
    <div class="info">
      <div class="brand-name">Gilded Slatworks</div>
      <div class="product-line">Shutters Shades Blinds</div>
      <div class="person-name">Daniel Trevick</div>
      <div class="person-role">Owner</div>
      <ul class="contact">
        <li>
          <svg viewBox="0 0 24 24" fill="none" stroke="currentColor" stroke-width="2.4" stroke-linecap="round" stroke-linejoin="round"><path d="M5 3h4l2 5-2.5 1.5a11 11 0 0 0 6 6L16 13l5 2v4a2 2 0 0 1-2 2A17 17 0 0 1 3 5a2 2 0 0 1 2-2z"/></svg>
          919-555-0148
        </li>
        <li>
          <svg viewBox="0 0 24 24" fill="none" stroke="currentColor" stroke-width="2.4"><circle cx="12" cy="12" r="9"/><path d="M3 12h18M12 3c3 3 3 15 0 18M12 3c-3 3-3 15 0 18"/></svg>
          gildedslatworks.com
        </li>
      </ul>
      <p class="services">Custom Interior &amp;<br>Exterior Window<br>Treatments</p>
    </div>
  </section>

</main>
</body>
</html>
```